High end Electrical/home automation Business Card

Need a card for a high end electrical and home automation company utilising the existing logo.
Phone
Email
Website

Like black look with raised detail. Don’t necessarily need to keep colour of logo it could be made grayscale or white etc

Target Market(s)

High end clients

Contact Information for Business Card

Brightmoor Electrical

Requirements
Must have
• Logo, phone, email, website, address

High end look
Nice to have
• Black background card
Raised font
Should not have
• Lots of colour

```html
<!DOCTYPE html>
<html lang="en">
<head>
<meta charset="utf-8">
<title>Brightmoor Electrical – Business Card</title>
<link rel="stylesheet" href="https://fonts.googleapis.com/css2?family=Lato:wght@400;700&display=swap">
<style>
  :root {
    --card-black: #2b2b2b;
    --ink-grey: #858585;
    --ink-soft: #7a7a7a;
  }
  html, body {
    margin: 0;
    padding: 0;
    width: 1200px;
    height: 685px;
    overflow: hidden;
    background: var(--card-black);
  }
  .card {
    position: relative;
    width: 1200px;
    height: 685px;
    background: var(--card-black);
    font-family: "Lato", Arial, sans-serif;
    color: var(--ink-grey);
  }
  .corner-bar {
    position: absolute;
    top: 0;
    right: 44px;
    width: 26px;
    height: 84px;
    background: var(--ink-grey);
  }
  .wordmark {
    position: absolute;
    top: 26px;
    left: 520px;
    margin: 0;
    font-size: 40px;
    font-weight: 700;
    letter-spacing: 0.5px;
    color: var(--ink-grey);
  }
  .brand-feature {
    position: absolute;
    left: 70px;
    top: 150px;
    width: 600px;
    height: 460px;
    display: flex;
    flex-direction: column;
    justify-content: center;
  }
  .brand-feature .brand-name {
    margin: 0;
    font-size: 92px;
    font-weight: 700;
    line-height: 1.05;
    color: var(--ink-grey);
  }
  .details {
    position: absolute;
    right: 60px;
    top: 140px;
    text-align: right;
  }
  .person-name {
    margin: 0;
    font-size: 40px;
    font-weight: 400;
    letter-spacing: 1.5px;
    text-transform: uppercase;
  }
  .person-title {
    margin: 0 0 34px;
    font-size: 24px;
    letter-spacing: 1px;
  }
  .address {
    margin: 0 0 26px;
    font-style: normal;
    font-size: 23px;
    line-height: 1.35;
    letter-spacing: 0.5px;
  }
  .contact-list {
    list-style: none;
    margin: 0;
    padding: 0;
    font-size: 23px;
    line-height: 1.4;
    letter-spacing: 0.5px;
  }
  .contact-list li {
    display: flex;
    justify-content: flex-end;
    align-items: center;
    gap: 14px;
  }
  .contact-icon {
    width: 20px;
    height: 20px;
    fill: var(--ink-grey);
    flex: none;
  }
</style>
</head>
<body>
<main class="card">
  <div class="corner-bar"></div>
  <p class="wordmark">Brightmoor Electrical</p>

  <div class="brand-feature">
    <p class="brand-name">Brightmoor<br>Electrical</p>
  </div>

  <section class="details">
    <h1 class="person-name">Daniel Hartley</h1>
    <p class="person-title">President</p>
    <address class="address">
      Brightmoor Electrical LLC<br>
      4120 Alder Crest Lane<br>
      Anchorage, Alaska 99504
    </address>
    <ul class="contact-list">
      <li>907-555-0142
        <svg class="contact-icon" viewBox="0 0 20 20" aria-hidden="true"><path d="M5 2l3 4-2 2c1 2 3 4 5 5l2-2 4 3-2 3C9 17 3 11 2 5z"/></svg>
      </li>
      <li>info@brightmoorelectrical.com
        <svg class="contact-icon" viewBox="0 0 20 20" aria-hidden="true"><path d="M2 5h16v10H2z M2 5l8 6 8-6" fill="none" stroke="#858585" stroke-width="2"/></svg>
      </li>
      <li>www.brightmoorelectrical.com
        <svg class="contact-icon" viewBox="0 0 20 20" aria-hidden="true"><circle cx="10" cy="10" r="8" fill="none" stroke="#858585" stroke-width="2"/><path d="M2 10h16M10 2c-3 3-3 13 0 16M10 2c3 3 3 13 0 16" fill="none" stroke="#858585" stroke-width="1.5"/></svg>
      </li>
    </ul>
  </section>
</main>
</body>
</html>
```